Web Design Project for a beach town business owner who supports new families with their babies.

I'm looking for a basic website with the following pages: home, about, services, FAQs, blog, and contact page. I have images and content ready to go.

Target Market(s)

Men and women between the ages of 22 and 42, growing families

Industry/Entity Type

Postpartum Doula

Coding

Number of Pages Required

Font styles to use
Serif
Other font styles liked:
• My logo font is "Nexa Bold" - so coordinating fonts with that are ideal

Colors
00AB8E
00BBA5
67D7C9
C6EFE9
E9F9F6
EE7325
F08F49
F5BC92
FAE3D3
FDF4ED

Requirements
Must have
• Warm and professional vibe, multicultural images, aligned with my branding colors and font ("Nexa Bold"; COLORS: light blue hex: #2FCEC2 R: 47 G: 206 B: 194 dark blue hex: #007C7C R: 0 G: 124 B: 124 orange hex: #F77B4E R: 247 G: 123 B: 78), good SEO
Should not have
• Ultra feminine images, baby bottles, cutesy images.

```html
<!DOCTYPE html>
<html lang="en">
<head>
<meta charset="utf-8">
<title>Harbor Nest Postpartum Care</title>
<link href="https://fonts.googleapis.com/css2?family=Montserrat:wght@600;700&family=Lato:wght@300;400&family=Raleway:wght@400&display=swap" rel="stylesheet">
<style>
:root{
  --teal-dark:#007C7C;
  --teal-light:#2FCEC2;
  --orange:#F77B4E;
  --icon-orange:#EE7325;
  --footer:#2b2b2b;
  --text:#333;
  --white:#fff;
}
*{margin:0;padding:0;box-sizing:border-box}
html,body{width:1200px;height:3199px;overflow:hidden;background:var(--white)}
body{position:relative;font-family:'Lato',sans-serif;color:var(--text)}
.abs{position:absolute}
.hero-photo{left:0;top:0;width:1200px;height:738px;background:radial-gradient(ellipse at 55% 45%,#6a6a6a 0%,#3a3a3a 55%,#1a1a1a 100%)}
.brand{left:75px;top:62px;display:flex;align-items:center;gap:10px;font-family:'Montserrat',sans-serif;font-weight:700;font-size:20px;color:var(--teal-light)}
.brand-dot{width:44px;height:44px;border-radius:50%;background:var(--white)}
.main-nav{top:78px;left:0;width:1200px;height:49px}
.main-nav a{position:absolute;top:0;height:49px;line-height:49px;font-family:'Montserrat',sans-serif;font-weight:700;font-size:17px;color:var(--white);text-decoration:none;letter-spacing:.3px}
.main-nav a.active{background:var(--teal-light);border-radius:25px;width:118px;text-align:center}
.hero-title{top:320px;left:0;width:1200px;text-align:center;font-family:'Montserrat',sans-serif;font-weight:600;font-size:36px;line-height:49px;color:var(--white)}
.hero-title .greet{color:var(--teal-light);display:block}
.intro-heading{top:802px;left:60px;width:1080px;text-align:center;font-family:'Montserrat',sans-serif;font-weight:600;font-size:26px;line-height:39px;color:var(--teal-dark)}
.photo-ring{width:522px;height:522px;border-radius:50%}
.body-copy{left:616px;width:520px;font-size:17px;line-height:31.4px;color:var(--text)}
.body-copy p+p{margin-top:15px}
.band-heading{top:1602px;left:60px;width:1080px;text-align:center;font-family:'Montserrat',sans-serif;font-weight:600;font-size:26px;line-height:38px;color:var(--white)}
.area-text{font-family:'Raleway',sans-serif;font-size:15px;line-height:24px;color:var(--white)}
.area-text.right-align{text-align:right}
.cta{left:616px;top:2736px;width:268px;height:70px;border-radius:35px;background:var(--orange);color:var(--white);font-family:'Montserrat',sans-serif;font-weight:600;font-size:22px;line-height:70px;text-align:center;text-decoration:none}
.site-footer{left:0;top:2956px;width:1200px;height:243px;background:var(--footer)}
.footer-nav{top:3018px;left:0;width:1200px;text-align:center;font-family:'Montserrat',sans-serif;font-weight:600;font-size:17px;color:var(--white)}
.footer-nav a{color:var(--white);text-decoration:none;margin:0 22px}
.copyright{top:3058px;left:0;width:1200px;text-align:center;font-family:'Montserrat',sans-serif;font-size:15px;color:var(--white);letter-spacing:.3px}
</style>
</head>
<body>

<header>
  <div class="abs hero-photo" role="img" aria-label="Black and white photo of parents holding their newborn"></div>
  <div class="abs brand"><span class="brand-dot"></span>Harbor Nest</div>
  <nav class="abs main-nav">
    <a class="active" style="left:358px" href="#">HOME</a>
    <a style="left:515px" href="#">ABOUT</a>
    <a style="left:648px" href="#">SERVICES</a>
    <a style="left:806px" href="#">FAQS</a>
    <a style="left:924px" href="#">BLOG</a>
    <a style="left:1042px" href="#">CONTACT</a>
  </nav>
  <h1 class="abs hero-title"><span class="greet">Congratulations on your birth &amp;</span>WELCOME TO HARBOR NEST<br>POSTPARTUM CARE!</h1>
</header>

<main>
  <h2 class="abs intro-heading">Hi, I’m Dana Reyes, a certified postpartum care expert and educator serving families of all varieties in the greater San Diego area and beyond.</h2>

  <svg class="abs" style="left:60px;top:905px" width="530" height="530" viewBox="0 0 530 530">
    <circle cx="265" cy="263" r="261" fill="#2FCEC2"/>
    <circle cx="270" cy="258" r="254" fill="#7a9a6a"/>
    <circle cx="270" cy="258" r="228" fill="none" stroke="#fff" stroke-width="2"/>
  </svg>
  <div class="abs photo-ring" style="left:69px;top:909px;background:transparent" role="img" aria-label="Portrait of the doula smiling outdoors"></div>

  <div class="abs body-copy" style="top:950px">
    <p>My passion as a professional is showing new parents just like you<br>that whether you’ve just had your first child or your fifth, you<br>cannot only survive your postpartum period (also known as the<br>4th trimester), but you and your family can THRIVE – with the<br>kind of compassionate, skilled, and targeted support for your<br>unique needs that only an expert can provide.<br>That’s where I come in.</p>
    <p>Did you know that, on average, new parents won’t see their<br>midwife or obstetrician until 6 weeks after giving birth to their<br>baby(ies)? Working with a postpartum care expert (also known as a<br>doula) can help fill in this gap in continuity of care by providing<br>individualized support for parents and families as they transition<br>to life with their new baby.</p>
  </div>

  <section>
    <svg class="abs" style="left:0;top:1474px" width="1200" height="840" viewBox="0 0 1200 840">
      <path d="M0 0 Q600 90 1200 0 L1200 839 Q600 750 0 839 Z" fill="#007C7C"/>
    </svg>
    <h2 class="abs band-heading">My work includes four key areas of support that are designed to positively<br>impact &nbsp;your postpartum period with your baby:</h2>

    <svg class="abs" style="left:404px;top:1775px" width="410" height="410" viewBox="0 0 410 410">
      <circle cx="205" cy="205" r="203" fill="#8a7f78"/>
      <circle cx="205" cy="205" r="193" fill="none" stroke="#fff" stroke-width="2"/>
    </svg>
    <div class="abs" style="left:406px;top:1777px;width:406px;height:406px;border-radius:50%" role="img" aria-label="Doula sitting with a family and their newborn"></div>

    <svg class="abs" style="left:330px;top:1747px" width="122" height="122" viewBox="0 0 122 122">
      <circle cx="61" cy="61" r="57" fill="none" stroke="#fff" stroke-width="3"/>
      <circle cx="61" cy="61" r="42" fill="#EE7325" stroke="#fff" stroke-width="3"/>
      <path d="M61 78 L44 61 A10 10 0 0 1 61 48 A10 10 0 0 1 78 61 Z" fill="none" stroke="#fff" stroke-width="2.5"/>
    </svg>
    <svg class="abs" style="left:762px;top:1747px" width="122" height="122" viewBox="0 0 122 122">
      <circle cx="61" cy="61" r="57" fill="none" stroke="#fff" stroke-width="3"/>
      <circle cx="61" cy="61" r="42" fill="#EE7325" stroke="#fff" stroke-width="3"/>
      <path d="M61 48 V72 M49 60 H73" stroke="#fff" stroke-width="3" stroke-linecap="round"/>
    </svg>
    <svg class="abs" style="left:276px;top:1944px" width="122" height="122" viewBox="0 0 122 122">
      <circle cx="61" cy="61" r="57" fill="none" stroke="#fff" stroke-width="3"/>
      <circle cx="61" cy="61" r="42" fill="#EE7325" stroke="#fff" stroke-width="3"/>
      <circle cx="61" cy="56" r="12" fill="none" stroke="#fff" stroke-width="2.5"/>
      <path d="M43 76 Q61 86 79 76" fill="none" stroke="#fff" stroke-width="2.5"/>
    </svg>
    <svg class="abs" style="left:817px;top:1944px" width="122" height="122" viewBox="0 0 122 122">
      <circle cx="61" cy="61" r="57" fill="none" stroke="#fff" stroke-width="3"/>
      <circle cx="61" cy="61" r="42" fill="#EE7325" stroke="#fff" stroke-width="3"/>
      <circle cx="61" cy="50" r="9" fill="none" stroke="#fff" stroke-width="2.5"/>
      <rect x="50" y="62" width="22" height="16" rx="6" fill="none" stroke="#fff" stroke-width="2.5"/>
    </svg>

    <p class="abs area-text right-align" style="left:70px;top:1754px;width:258px">I provide practical, evidence-based information about baby care and help identify what is normal and what is outside the range of normal for parent(s) and baby</p>
    <p class="abs area-text" style="left:885px;top:1754px;width:240px">I prioritize the mental and emotional health of parent(s) and help identify potential warning signs that indicate that medical care may be needed.</p>
    <p class="abs area-text right-align" style="left:80px;top:1950px;width:193px;line-height:20.5px">I enhance bonding and attachment between parents(s) and baby in the areas of feeding, soothing, learning baby’s cues, babywearing, and playing with baby.</p>
    <p class="abs area-text" style="left:940px;top:1950px;width:180px">I offer hands-on support with baby(ies), older siblings, pets, and light home upkeep and meal preparation.</p>
  </section>

  <svg class="abs" style="left:60px;top:2358px" width="530" height="530" viewBox="0 0 530 530">
    <circle cx="265" cy="265" r="261" fill="#2FCEC2"/>
    <circle cx="270" cy="258" r="254" fill="#8a8a5a"/>
    <circle cx="270" cy="258" r="228" fill="none" stroke="#fff" stroke-width="2"/>
  </svg>
  <div class="abs photo-ring" style="left:69px;top:2362px" role="img" aria-label="Family with a child smiling together outdoors by a tree"></div>

  <div class="abs body-copy" style="top:2418px">
    <p>Families who work with me report feeling more connected,<br>happy, and informed than their parenting-veteran friends and<br>family members – both during the time that I work with<br>them and beyond.</p>
    <p>Struggle is a normal part of growth and learning. Your postpartum<br>period is a time for healing and recovering from birth, bonding<br>with your baby, and establishing a healthy feeding relationship in<br>whatever way works best for your family. Let me show you how to<br>remove the struggle from this magical time!</p>
  </div>
  <a class="abs cta" href="#">Let’s Get Started</a>
</main>

<footer>
  <div class="abs site-footer"></div>
  <nav class="abs footer-nav">
    <a href="#">HOME</a><a href="#">ABOUT</a><a href="#">SERVICES</a><a href="#">FAQS</a><a href="#">BLOG</a><a href="#">CONTACT</a>
  </nav>
  <p class="abs copyright">Copyright © 2021 Company Name All Rights Reserved</p>
  <svg class="abs" style="left:500px;top:3107px" width="200" height="38" viewBox="0 0 200 38">
    <g fill="none" stroke="#fff" stroke-width="1.5">
      <circle cx="19" cy="19" r="17"/><circle cx="59" cy="19" r="17"/><circle cx="99" cy="19" r="17"/><circle cx="140" cy="19" r="17"/><circle cx="181" cy="19" r="17"/>
    </g>
  </svg>
</footer>

</body>
</html>
```